Business Card Design for Marketing Firm

Looking for business card design for higher end marketing firm. Clean but impressionable/trendy. We are a marketing firm that represents manufacturers in the foodservice equipment and supply industry. Our customers are end users such has hotels, restaurants, country clubs, convention centers and casinos as well as distributors of restaurants supplies and equipment, and manufacturers of foodservice equipment and supplies.
Target Market(s)
Hotels, Restaurants, Supply & Equipment Distributors, Foodservice Manufacturers
Industry/Entity Type
Foodservice/Hospitality
Contact Information for Business Card
Name, Title, Contact Number, Email, Website, Social Media, Address
Requirements
Must have
- Clean & Simple but Serious and Impressionable

```html
<!DOCTYPE html>
<html lang="en">
<head>
<meta charset="utf-8">
<title>Harbor Table Reps – Business Card</title>
<link rel="stylesheet" href="https://fonts.googleapis.com/css2?family=Montserrat:wght@700;800&family=Open+Sans:wght@400;600&display=swap">
<style>
  :root {
    --navy: #262a7e;
    --ink: #3a3a44;
    --paper: #ffffff;
    --backdrop: #e9e8ec;
    --rule: #262a7e;
  }
  * { box-sizing: border-box; margin: 0; padding: 0; }
  html, body { width: 1200px; height: 834px; overflow: hidden; }
  body {
    background: var(--backdrop);
    position: relative;
    font-family: "Open Sans", sans-serif;
  }
  .card {
    position: absolute;
    top: 267px;
    width: 520px;
    height: 300px;
    background: var(--paper);
    box-shadow: 0 6px 22px rgba(0,0,0,0.12);
    overflow: hidden;
  }
  .card--front { left: 50px; }
  .card--back { left: 630px; }

  .brand {
    display: flex;
    align-items: center;
    gap: 10px;
    color: var(--navy);
    font-family: "Montserrat", sans-serif;
    font-weight: 700;
    letter-spacing: 0.06em;
    text-transform: uppercase;
    line-height: 1.15;
  }
  .brand__dot {
    width: 14px; height: 14px;
    border-radius: 50%;
    background: var(--navy);
    flex: none;
  }

  /* back */
  .card--back .brand {
    position: absolute;
    left: 0; right: 0; top: 104px;
    justify-content: center;
    font-size: 26px;
  }
  .card--back .brand__dot { width: 18px; height: 18px; }
  .social {
    position: absolute;
    top: 178px; left: 0; right: 0;
    display: flex; justify-content: center; gap: 8px;
    list-style: none;
  }
  .social li {
    width: 16px; height: 16px; border-radius: 50%;
    background: var(--navy);
  }

  /* front */
  .card--front .brand {
    position: absolute;
    left: 28px; top: 92px;
    width: 200px;
    font-size: 17px;
  }
  .divider {
    position: absolute;
    left: 246px; top: 56px;
    width: 1px; height: 170px;
    background: var(--rule);
  }
  .contact {
    position: absolute;
    left: 266px; top: 58px;
    color: var(--ink);
  }
  .contact__name {
    font-family: "Montserrat", sans-serif;
    font-weight: 800;
    font-size: 19px;
    color: var(--navy);
    letter-spacing: 0.02em;
  }
  .contact__title { font-size: 13px; margin-bottom: 6px; }
  .contact__address { font-size: 12px; font-style: normal; line-height: 1.4; margin-bottom: 8px; }
  .contact__list { list-style: none; font-size: 12px; line-height: 1.6; }
  .contact__list li { display: flex; align-items: center; gap: 7px; }
  .contact__list svg { width: 11px; height: 11px; fill: var(--navy); flex: none; }

  .band {
    position: absolute;
    left: 0; bottom: 0;
    width: 520px; height: 40px;
  }
  .band__web {
    position: absolute;
    right: 24px; bottom: 10px;
    color: #fff;
    font-size: 14px;
    letter-spacing: 0.02em;
  }
</style>
</head>
<body>

<section class="card card--front" aria-label="Card front">
  <div class="brand"><span class="brand__dot"></span><span>Harbor Table Reps</span></div>
  <div class="divider"></div>
  <div class="contact">
    <h1 class="contact__name">DANIEL REYES</h1>
    <p class="contact__title">Managing Director</p>
    <address class="contact__address">Your address, City<br>State, Zip 1234</address>
    <ul class="contact__list">
      <li><svg viewBox="0 0 24 24"><path d="M6.6 10.8a15 15 0 0 0 6.6 6.6l2.2-2.2a1 1 0 0 1 1-.25 11.4 11.4 0 0 0 3.6.57 1 1 0 0 1 1 1V20a1 1 0 0 1-1 1A17 17 0 0 1 3 4a1 1 0 0 1 1-1h3.5a1 1 0 0 1 1 1c0 1.25.2 2.45.57 3.57a1 1 0 0 1-.25 1z"/></svg>2233333333</li>
      <li><svg viewBox="0 0 24 24"><path d="M7 1h10a2 2 0 0 1 2 2v18a2 2 0 0 1-2 2H7a2 2 0 0 1-2-2V3a2 2 0 0 1 2-2zm0 3v14h10V4z"/></svg>0000000000</li>
      <li><svg viewBox="0 0 24 24"><path d="M2 5h20v14H2zm2 2v.5l8 5 8-5V7z"/></svg>hello@harbortable.com</li>
    </ul>
  </div>
  <svg class="band" viewBox="0 0 520 40" aria-hidden="true">
    <polygon points="0,30 210,30 230,0 520,0 520,40 0,40" fill="var(--navy)"/>
  </svg>
  <span class="band__web">www.harbortable.com</span>
</section>

<section class="card card--back" aria-label="Card back">
  <div class="brand"><span class="brand__dot"></span><span>Harbor Table Reps</span></div>
  <ul class="social" aria-label="Social media">
    <li></li><li></li><li></li><li></li><li></li><li></li>
  </ul>
</section>

</body>
</html>
```